New iOS App design for Boston Startup

We are looking for a new app design for our iPhone app. The current app's design feels outdated and we like to add lots of new functionality and a new navigation as well. A complete overhaul therefore!
We want you to design 5 screens that will have changed the most. The complete wireframes of these 5 pages are attached in the requirements document.
Once the winning design is selected we will award the winner with the designing all other screens (40-50 screens based on the same design). This will be a separate project worth $1000. The winning designer can get more follow up work if both sides are happy about the cooperation.
We will give feedback as soon as the first screen has been uploaded for review. Final decision will be made only after all 5 screens are finished.
We hope you give it your best!
Note: will only communicate through PixelHarbor (no skype),
Updates
Reason: Want to give designers a chance to submit their designs as I understand from some, the deadline is too close.
I have raised the award and introduced a 2nd price as well to make it worth your time. I hope you give it your best shot.
Reason: A few of you have asked for an extension of the deadline as time is running out. I will extend by one day. Tell me if you need more.
Industry/Entity Type
Startup
Requirements
Must have
- At least 1 screen before we can give you feedback.
Nice to have
- multiple options of 1 screen to get to a desirable design

```html
<!DOCTYPE html>
<html lang="en">
<head>
<meta charset="utf-8">
<title>Dashboard Screen</title>
<link href="https://fonts.googleapis.com/css2?family=Open+Sans:wght@300;400;600;700&display=swap" rel="stylesheet">
<style>
  :root {
    --brand-blue: #2a8ad8;
    --brand-blue-dark: #1f74b8;
    --button-blue: #2c8fdb;
    --alert-red: #e8453c;
    --stat-green: #a6e23a;
    --tab-dark: #2b2b2b;
    --tab-icon: #d9d9d9;
    --up-next-grey: #6b6b6b;
    --page-bg: #ffffff;
    --stage-bg: #f2f2f2;
    --text-dark: #222222;
    --white: #ffffff;
  }
  * { box-sizing: border-box; margin: 0; padding: 0; }
  html, body {
    width: 1200px; height: 1041px; overflow: hidden;
    background: var(--stage-bg);
    font-family: "Open Sans", sans-serif;
  }
  .stage {
    width: 1200px; height: 1041px;
    display: flex; align-items: center; justify-content: center;
  }
  .screen {
    width: 320px; height: 568px;
    background: var(--page-bg);
    position: relative;
    overflow: hidden;
    transform: scale(1.75);
    box-shadow: 0 2px 10px rgba(0,0,0,0.12);
  }
  .header { background: var(--brand-blue); color: var(--white); }
  .status-bar {
    height: 20px; display: flex; align-items: center; justify-content: space-between;
    padding: 0 6px; font-size: 9px; font-weight: 600; position: relative;
  }
  .status-bar .carrier { display: flex; align-items: center; gap: 4px; }
  .status-bar .time { position: absolute; left: 0; right: 0; text-align: center; pointer-events: none; }
  .status-bar .battery { display: flex; align-items: center; gap: 3px; }
  .battery-icon { width: 18px; height: 8px; border: 1px solid var(--white); border-radius: 1px; padding: 1px; }
  .battery-icon span { display: block; width: 100%; height: 100%; background: var(--white); }
  .nav-row { height: 34px; display: flex; align-items: center; padding: 0 10px; position: relative; }
  .nav-title { position: absolute; left: 0; right: 0; text-align: center; font-size: 14px; font-weight: 600; }
  .score-row { display: flex; align-items: baseline; justify-content: center; gap: 8px; padding-top: 2px; }
  .score-label { font-size: 26px; font-weight: 300; }
  .score-value { font-size: 50px; font-weight: 700; line-height: 1; }
  .score-change { font-size: 18px; color: var(--alert-red); font-weight: 400; }
  .stats-row {
    display: flex; align-items: center; height: 44px; margin-top: 4px;
    border-top: 1px solid rgba(255,255,255,0.25); position: relative; padding: 0 14px;
  }
  .stats-arrow { position: absolute; top: 15px; }
  .stats-arrow.prev { left: 3px; }
  .stats-arrow.next { right: 3px; }
  .stat { flex: 1; text-align: center; border-right: 1px solid rgba(255,255,255,0.4); line-height: 1.15; }
  .stat:last-child { border-right: none; flex: 0.45; overflow: hidden; white-space: nowrap; text-align: left; padding-left: 6px; }
  .stat-value { font-size: 11px; font-weight: 700; }
  .stat-value .main { color: var(--stat-green); }
  .stat-label { font-size: 9px; opacity: 0.9; }
  .actions { padding: 16px 20px 0; display: flex; flex-direction: column; gap: 10px; }
  .action-button {
    height: 40px; background: var(--button-blue); color: var(--white);
    display: flex; align-items: center; justify-content: center;
    font-size: 15px; font-weight: 400; border-radius: 2px;
  }
  .up-next-label { text-align: center; font-size: 13px; color: var(--text-dark); margin: 14px 0 6px; }
  .up-next-bar {
    margin: 0 20px; height: 38px; background: var(--up-next-grey); color: var(--white);
    display: flex; align-items: center; justify-content: center; font-size: 14px; border-radius: 2px;
  }
  .tab-bar {
    position: absolute; left: 0; right: 0; bottom: 0; height: 52px;
    background: var(--tab-dark); display: flex;
  }
  .tab { flex: 1; display: flex; flex-direction: column; align-items: center; justify-content: center; gap: 3px; color: var(--tab-icon); font-size: 8px; font-weight: 600; }
  .tab svg { width: 22px; height: 18px; }
  .tab.active svg { color: var(--brand-blue); }
</style>
</head>
<body>
<div class="stage">
  <main class="screen">
    <header class="header">
      <div class="status-bar">
        <span class="carrier">LUMA
          <svg width="10" height="8" viewBox="0 0 10 8" aria-label="Wi-Fi"><path d="M1 3a6 6 0 0 1 8 0M2.5 4.6a4 4 0 0 1 5 0" stroke="#fff" stroke-width="1.1" fill="none"/><circle cx="5" cy="6.6" r="1" fill="#fff"/></svg>
        </span>
        <span class="time">4:21 PM</span>
        <span class="battery">100% <span class="battery-icon"><span></span></span></span>
      </div>
      <div class="nav-row">
        <svg width="20" height="14" viewBox="0 0 20 14" aria-label="Menu"><rect y="0" width="20" height="2" fill="#fff"/><rect y="6" width="20" height="2" fill="#fff"/><rect y="12" width="20" height="2" fill="#fff"/></svg>
        <span class="nav-title">Welcome back, Noam</span>
      </div>
      <div class="score-row">
        <span class="score-label">Score</span>
        <span class="score-value">650</span>
        <span class="score-change">-18</span>
      </div>
      <div class="stats-row">
        <svg class="stats-arrow prev" width="8" height="14" viewBox="0 0 8 14"><path d="M7 1 1 7l6 6" stroke="#fff" stroke-width="2" fill="none"/></svg>
        <div class="stat"><div class="stat-value"><span class="main">34%</span> +4</div><div class="stat-label">Completion</div></div>
        <div class="stat"><div class="stat-value"><span class="main">20</span> +3</div><div class="stat-label">Sessions</div></div>
        <div class="stat"><div class="stat-value"><span class="main">18</span> +10</div><div class="stat-label">Sessions</div></div>
        <div class="stat"><div class="stat-value">&nbsp;</div><div class="stat-label">This w</div></div>
        <svg class="stats-arrow next" width="8" height="14" viewBox="0 0 8 14"><path d="M1 1l6 6-6 6" stroke="#fff" stroke-width="2" fill="none"/></svg>
      </div>
    </header>

    <section class="actions">
      <div class="action-button">Analytics</div>
      <div class="action-button">Course Overview</div>
      <div class="action-button">Days Until test 33</div>
    </section>

    <p class="up-next-label">Up Next:</p>
    <div class="up-next-bar">Sentence Correction Lesson 4</div>

    <nav class="tab-bar">
      <div class="tab">
        <svg viewBox="0 0 22 18"><path d="M11 1 1 9h3v8h5v-5h4v5h5V9h3z" fill="currentColor"/></svg>
        Home
      </div>
      <div class="tab">
        <svg viewBox="0 0 22 18"><path d="M2 3c3-1 6-1 9 1v13c-3-2-6-2-9-1zM20 3c-3-1-6-1-9 1v13c3-2 6-2 9-1z" fill="none" stroke="currentColor" stroke-width="1.5"/></svg>
        Theory
      </div>
      <div class="tab active">
        <svg viewBox="0 0 22 18"><path d="M2 3l6 6-6 6zM8 3l6 6-6 6zM14 3l6 6-6 6z" fill="currentColor"/></svg>
        Practice
      </div>
      <div class="tab">
        <svg viewBox="0 0 22 18"><rect x="1" y="4" width="20" height="11" rx="5" fill="currentColor"/><rect x="5" y="8.5" width="5" height="2" fill="#2b2b2b"/><rect x="6.5" y="7" width="2" height="5" fill="#2b2b2b"/><circle cx="15" cy="8" r="1.2" fill="#2b2b2b"/><circle cx="17" cy="11" r="1.2" fill="#2b2b2b"/></svg>
        Games
      </div>
      <div class="tab">
        <svg viewBox="0 0 22 18"><rect x="3" y="2" width="16" height="15" rx="3" fill="currentColor"/><path d="M7 10l3 3 6-7" stroke="#2b2b2b" stroke-width="2" fill="none"/></svg>
        Test
      </div>
    </nav>
  </main>
</div>
</body>
</html>
```